business card - Helicopter Flight Services, Flight School, etc.

We need a business card design for a new helicopter service.

We offer Helicopter Flight Services, Aerial Filming & Photography, Flight School, and Helicopter Tours. In that order.

Summit BladeAir, Inc.
Dennis Tollerby
SummitBladeair@Kestmail.com
626-418-7352

Based at the Brenwick Airport in Van Nuys, CA. The final design should communicate integrity and safety. Pictures or logos at your discretion.

Card back side - surprise me.

```html
<!DOCTYPE html>
<html lang="en">
<head>
<meta charset="utf-8">
<title>Summit BladeAir, Inc. — Business Card</title>
<link rel="stylesheet" href="https://fonts.googleapis.com/css2?family=Bodoni+Moda:ital,wght@0,500;0,600;1,500&family=Arimo:wght@400&display=swap">
<style>
  :root {
    --page-bg: #e7e4df;
    --card-white: #ffffff;
    --card-shade: #eeeeee;
    --ink: #141414;
    --ink-soft: #2a2a2a;
    --accent-blue: #3b66c4;
    --sky-light: #b9c1ca;
    --sky-dark: #98a3af;
    --icon-bg: #1d1d1d;
    --ghost: #d4d4d4;
  }
  * { box-sizing: border-box; margin: 0; padding: 0; }
  html, body { width: 1200px; height: 892px; overflow: hidden; }
  body {
    background: var(--page-bg);
    position: relative;
    font-family: "Arimo", Arial, sans-serif;
    color: var(--ink);
  }
  .card {
    position: absolute;
    top: 292px;
    width: 540px;
    height: 308px;
    background: linear-gradient(160deg, var(--card-white) 55%, var(--card-shade));
    box-shadow: 0 6px 18px rgba(0,0,0,0.18);
    overflow: hidden;
  }
  .card--front { left: 40px; }
  .card--back { left: 620px; }

  /* Front */
  .front-art { position: absolute; inset: 0; }
  .company-name {
    position: absolute;
    font-family: "Bodoni Moda", "Times New Roman", serif;
    font-weight: 600;
    text-transform: uppercase;
    letter-spacing: 0.5px;
  }
  .card--front .company-name { left: 196px; top: 24px; font-size: 19px; }
  .holder-name {
    position: absolute;
    right: 150px; top: 92px;
    font-family: "Bodoni Moda", "Times New Roman", serif;
    font-weight: 600;
    font-size: 22px;
  }
  .contact-list {
    position: absolute;
    right: 18px; top: 150px;
    list-style: none;
    text-align: right;
    font-size: 14.5px;
    line-height: 22px;
    color: var(--ink-soft);
  }
  .contact-list li { display: flex; justify-content: flex-end; align-items: center; gap: 10px; }
  .contact-list .no-icon { padding-right: 24px; }
  .contact-icon { width: 14px; height: 14px; flex: none; }

  /* Back */
  .back-ghost {
    position: absolute;
    left: 300px; top: 70px;
    width: 190px; height: 200px;
  }
  .card--back .company-name {
    left: 0; right: 0; top: 112px;
    text-align: center;
    font-size: 34px;
    font-weight: 500;
  }
  .tagline {
    position: absolute;
    left: 0; right: 0; top: 166px;
    text-align: center;
    font-family: "Bodoni Moda", "Times New Roman", serif;
    font-style: italic;
    font-size: 19px;
  }
</style>
</head>
<body>

<section class="card card--front" aria-label="Business card front">
  <svg class="front-art" width="540" height="308" viewBox="0 0 540 308">
    <defs>
      <linearGradient id="skyFill" x1="0" y1="0" x2="0" y2="1">
        <stop offset="0" stop-color="var(--sky-light)"/>
        <stop offset="1" stop-color="var(--sky-dark)"/>
      </linearGradient>
    </defs>
    <path role="img" aria-label="Photo of a helicopter flying in front of a full moon against a grey sky"
          d="M0 0 H188 C200 90 230 200 300 308 H0 Z" fill="url(#skyFill)"/>
    <path d="M188 0 C200 90 230 200 300 308" fill="none" stroke="var(--accent-blue)" stroke-width="6"/>
  </svg>

  <h1 class="company-name">Summit BladeAir, Inc.</h1>
  <p class="holder-name">Dennis Tollerby</p>

  <ul class="contact-list">
    <li>626-418-7352
      <svg class="contact-icon" viewBox="0 0 14 14" aria-hidden="true"><rect width="14" height="14" fill="var(--icon-bg)"/><path d="M4 3.5 L5.6 3.5 L6.2 5.4 L5.3 6.1 Q6.2 7.9 7.9 8.7 L8.6 7.8 L10.5 8.4 L10.5 10 Q6 10.3 4 5.4 Z" fill="#fff"/></svg>
    </li>
    <li>SummitBladeair@Kestmail.com
      <svg class="contact-icon" viewBox="0 0 14 14" aria-hidden="true"><rect width="14" height="14" fill="var(--icon-bg)"/><rect x="3" y="4.5" width="8" height="5.5" fill="#fff"/><path d="M3 4.5 L7 7.6 L11 4.5" fill="none" stroke="var(--icon-bg)" stroke-width="0.9"/></svg>
    </li>
    <li>4870 W. Larkhaven Blvd. Ste.B
      <svg class="contact-icon" viewBox="0 0 14 14" aria-hidden="true"><rect width="14" height="14" fill="var(--icon-bg)"/><path d="M7 11.5 L4.3 6.8 A3 3 0 1 1 9.7 6.8 Z" fill="#fff"/><circle cx="7" cy="5.6" r="1.1" fill="var(--icon-bg)"/></svg>
    </li>
    <li class="no-icon">Brenwick, CA 91622</li>
  </ul>
</section>

<section class="card card--back" aria-label="Business card back">
  <svg class="back-ghost" viewBox="0 0 190 200" role="img" aria-label="Large faint aircraft silhouette in the background">
    <rect width="190" height="200" rx="14" fill="var(--ghost)" opacity="0.45"/>
  </svg>
  <h2 class="company-name">Summit BladeAir, Inc.</h2>
  <p class="tagline">Tour guide · Heliport</p>
</section>

</body>
</html>
```